House-share and Room Rental Website (With Focus on the Bedroom Landing Page)

Looking for website design for our House-share (executive accommodation) and room rental business.

Our company name is: Lodgivo could also be written as LodGivo or lodgivo. Either is fine .. just looking for a nice clean catchy logo to go with the design.

EXAMPLES
These are examples of other websites in this field that are doing well. this is a kind of baseline.
https://nestpartners-example.com.au/
https://www.bunkora-example.com/
https://www.dwelzy-example.com/
https://www.habiquo-example.net/
https://www.cohabiscout-example.com.au/

Our business model is to rent rooms to people looking for high-quality accommodation. We fill the gap between those looking to rent rooms and those with rooms to rent. However, our model is slightly different from those already on the market as we looking to fill a massive gap in the market delivering upmarket rooms for rent.(Executive Accommodation) also in the back end will be coupled with a self management process in the back end.

We offer executive style accommodation that stands out above the rest. With special extras like fire safety.. and management processes that create happier homes. We are looking for a web design package that can help us grow and scale our business. We need a design that is captivating

Our MAIN focus is having a room landing page that stands out from the rest... The core of our business will rely on the promotion of the rooms in a share house... so the whole design relies on the BEDROOM landing page to drive results.

Target Market(s)

We have 2 markets we are aiming at ... the first market is people offering rooms to rent who want the highest rental return. The second market is people looking to rent safe, high-quality rooms, in houses that are well managed and looked after.

Industry/Entity Type

Share Economy

Logo Text

LodGivo

Number of Pages Required

5+ page

Font styles to use
Sans Serif

Colors
3276b5

Requirements
Must have
• A messaging system whereby we can create direct communication between those offering rooms and those looking for rooms.
• A call to action that says " Schedule an Inspection"
• Landing page for promoting rooms
• A home page for showing stock.
• Profile page for those selling rooms
• Profile page for those looking for rooms.
• A scheduling calendar for booking inspections
Nice to have
• Pages where new residents can lock in a room.. pay bond and rents.. and sign contracts
• Notifications
• SMS capabilities in the backend.
Should not have
• No script or handwriting fonts.

```html
<!DOCTYPE html>
<html lang="en">
<head>
<meta charset="utf-8">
<title>LodGivo – Bedroom</title>
<link href="https://fonts.googleapis.com/css2?family=Raleway:wght@400;500;600;700&family=Open+Sans:wght@400;600&display=swap" rel="stylesheet">
<style>
:root{
  --brand:#2f62ac;
  --brand-title:#3276b5;
  --page:#e8e8e8;
  --card:#ffffff;
  --text:#4a4a4a;
  --muted:#8a8a8a;
  --line:#dcdcdc;
  --circle:#e6e6e6;
  --icon:#555555;
  --footer:#2b2b2b;
  --footer-text:#bdbdbd;
  --footer-rule:#4a4a4a;
  --search:#f0f0f0;
  --car-tab:#dde9f7;
}
*{box-sizing:border-box;margin:0;padding:0}
html,body{width:1200px;height:2184px;overflow:hidden}
body{background:var(--page);font-family:"Raleway",sans-serif;color:var(--text);position:relative}

.site-header{position:absolute;left:0;top:0;width:1200px;height:80px;background:var(--brand)}
.site-logo{position:absolute;left:142px;top:16px;font-size:40px;font-weight:700;color:#fff;letter-spacing:-.3px;line-height:48px}
.main-nav{position:absolute;left:530px;top:29px}
.main-nav a{color:#fff;text-decoration:none;font-size:14px;position:absolute;white-space:nowrap}
.cta-button{position:absolute;left:879px;top:18px;width:176px;height:44px;border:1.5px solid #fff;border-radius:3px;color:#fff;font-size:14px;display:flex;align-items:center;justify-content:center}

.listing{position:absolute;left:144px;top:124px;width:912px;height:1713px;background:var(--card)}
.hero{position:absolute;left:0;top:0;width:912px;height:520px;background:linear-gradient(115deg,#cfc9c0 0%,#ece9e3 35%,#b9a58c 55%,#6e5a46 80%,#3d342c 100%)}
.hero-expand{position:absolute;right:10px;top:13px}
.hero-caption{position:absolute;left:0;top:412px;width:912px;text-align:center;color:#fff;font-size:19px;font-weight:500;text-shadow:0 1px 3px rgba(0,0,0,.45)}
.hero-strip{position:absolute;left:0;top:448px;width:912px;height:72px;background:rgba(20,20,20,.9)}
.thumb{position:absolute;top:4px;width:96px;height:55px}
.strip-arrow{position:absolute;top:20px}

.section-title{position:absolute;left:0;width:912px;text-align:center;color:var(--brand-title);font-size:24px;font-weight:500}
.info-row{position:absolute;font-size:13px;color:var(--text)}
.divider{position:absolute;left:0;width:912px;height:1px;background:var(--line)}

.amenity{position:absolute;width:120px;text-align:center}
.amenity-circle{width:96px;height:96px;border-radius:50%;background:var(--circle);margin:0 auto;display:flex;align-items:center;justify-content:center}
.amenity-label{margin-top:15px;font-size:13px;color:var(--text)}

.search-bar{position:absolute;left:24px;top:1231px;width:863px;height:58px;background:var(--search);display:flex}
.search-input{width:497px;display:flex;align-items:center;padding-left:22px;color:#aaa;font-size:16px;gap:8px}
.transport-tab{display:flex;align-items:center;justify-content:center;gap:8px;font-size:19px;color:#777;font-weight:500;border-left:1px solid #dcdcdc}
.transport-tab.active{background:var(--car-tab);color:var(--brand-title)}
.map{position:absolute;left:24px;top:1289px;width:863px;height:399px;background:linear-gradient(135deg,#e4e4e4,#cfcfcf 50%,#dedede)}

.site-footer{position:absolute;left:0;top:1888px;width:1200px;height:296px;background:var(--footer);font-family:"Open Sans",sans-serif}
.footer-heading{position:absolute;top:50px;font-family:"Raleway",sans-serif;color:#eee;font-size:19px}
.footer-link{position:absolute;font-size:11.5px;color:var(--footer-text)}
.newsletter{position:absolute;left:670px;top:92px;width:218px;height:44px;background:#e9e9e9;display:flex;align-items:center;justify-content:space-between;padding:0 12px 0 16px;font-size:11px;color:#333}
.social{position:absolute;top:96px;width:18px;height:18px;border-radius:50%;background:#8c8c8c}
.footer-rule{position:absolute;left:144px;top:221px;width:912px;height:1px;background:var(--footer-rule)}
.copyright{position:absolute;left:0;top:253px;width:1200px;text-align:center;font-size:11.5px;color:#ddd}
</style>
</head>
<body>

<header class="site-header">
  <div class="site-logo">LodGivo</div>
  <nav class="main-nav">
    <a style="left:0">Home</a>
    <a style="left:68px">Profile</a>
    <a style="left:138px">Bond &amp; Rents</a>
    <a style="left:251px">Contact Us</a>
  </nav>
  <div class="cta-button">Schedule an Inspection</div>
</header>

<main class="listing">
  <div class="hero" role="img" aria-label="Photo of a bright bedroom with a made bed, bedside lamps, dresser and large mirror">
    <svg class="hero-expand" width="28" height="28" viewBox="0 0 28 28"><rect width="28" height="28" fill="#333"/><g stroke="#fff" stroke-width="2.2" fill="none"><path d="M6 11V6h5M17 6h5v5M22 17v5h-5M11 22H6v-5M6 6l6 6M22 6l-6 6M22 22l-6-6M6 22l6-6"/></g></svg>
    <div class="hero-caption">24 Building name, Street name, City Zipcode &nbsp; / &nbsp; Rental Price : $200 &nbsp; / &nbsp; Utilities : Included</div>
    <div class="hero-strip">
      <svg class="strip-arrow" style="left:12px" width="18" height="26" viewBox="0 0 18 26"><path d="M14 3L4 13l10 10" stroke="#fff" stroke-width="4" fill="none"/></svg>
      <div class="thumb" style="left:44px;background:#c9c9c9" role="img" aria-label="Thumbnail of a white living room"></div>
      <div class="thumb" style="left:148px;background:#b8a373" role="img" aria-label="Thumbnail of a room with a yellow chair"></div>
      <div class="thumb" style="left:252px;background:#4a4440" role="img" aria-label="Thumbnail of a dark dining area"></div>
      <div class="thumb" style="left:356px;background:#2f3a40" role="img" aria-label="Thumbnail of a shelf against a dark wall"></div>
      <div class="thumb" style="left:460px;background:#6d7a82" role="img" aria-label="Thumbnail of a lounge with a sofa"></div>
      <div class="thumb" style="left:564px;background:#bdbdbd" role="img" aria-label="Thumbnail of a TV on a white cabinet"></div>
      <div class="thumb" style="left:668px;background:#e1e1e1" role="img" aria-label="Thumbnail of an air conditioner in a room"></div>
      <div class="thumb" style="left:772px;background:#3c4a5c" role="img" aria-label="Thumbnail of a car in a garage"></div>
      <svg class="strip-arrow" style="left:884px" width="18" height="26" viewBox="0 0 18 26"><path d="M4 3l10 10L4 23" stroke="#fff" stroke-width="4" fill="none"/></svg>
    </div>
  </div>

  <h2 class="section-title" style="top:570px">Bedroom Information</h2>
  <div class="info-row" style="left:25px;top:622px">Gender Preference</div><div class="info-row" style="left:152px;top:622px">:</div><div class="info-row" style="left:167px;top:622px">Male</div>
  <div class="info-row" style="left:25px;top:654px">Size of room</div><div class="info-row" style="left:152px;top:654px">:</div><div class="info-row" style="left:167px;top:654px">300 Sqft</div>
  <div class="info-row" style="left:25px;top:686px">Bathroom</div><div class="info-row" style="left:152px;top:686px">:</div><div class="info-row" style="left:167px;top:686px">Shared</div>
  <div class="info-row" style="left:25px;top:718px">Parking</div><div class="info-row" style="left:152px;top:718px">:</div><div class="info-row" style="left:167px;top:718px">Private</div>

  <div class="info-row" style="left:344px;top:622px">Smoking/non-smoking</div><div class="info-row" style="left:499px;top:622px">:</div><div class="info-row" style="left:513px;top:622px">Yes</div>
  <div class="info-row" style="left:344px;top:654px">Minimum Contract</div><div class="info-row" style="left:499px;top:654px">:</div><div class="info-row" style="left:513px;top:654px">3 months</div>
  <div class="info-row" style="left:344px;top:686px">Bed size</div><div class="info-row" style="left:499px;top:686px">:</div><div class="info-row" style="left:513px;top:686px">King Size</div>
  <div class="info-row" style="left:344px;top:718px">Type of housemates</div><div class="info-row" style="left:499px;top:718px">:</div><div class="info-row" style="left:513px;top:718px">Professionals</div>

  <div class="info-row" style="left:711px;top:622px">Room Type</div><div class="info-row" style="left:817px;top:622px">:</div><div class="info-row" style="left:833px;top:622px">Shared</div>
  <div class="info-row" style="left:711px;top:654px">Internet Speed</div><div class="info-row" style="left:817px;top:654px">:</div><div class="info-row" style="left:833px;top:654px">164 kbps</div>

  <div class="divider" style="top:799px"></div>

  <h2 class="section-title" style="top:858px">Room Amenities</h2>
  <div class="amenity" style="left:20px;top:905px"><div class="amenity-circle"><svg width="50" height="50" viewBox="0 0 50 50" fill="none" stroke="#555" stroke-width="1.8"><path d="M21 6h8l2 8H19zM25 14v6"/><rect x="9" y="20" width="32" height="22" rx="2"/><path d="M9 31h32M22 26h6M22 37h6M12 42v4M38 42v4"/></svg></div><div class="amenity-label">Furnished</div></div>
  <div class="amenity" style="left:145px;top:905px"><div class="amenity-circle"><svg width="56" height="50" viewBox="0 0 56 50" fill="none" stroke="#555" stroke-width="1.8"><rect x="4" y="8" width="48" height="30" rx="2"/><rect x="8" y="12" width="40" height="22"/><path d="M22 38l-2 6h16l-2-6"/></svg></div><div class="amenity-label">TV</div></div>
  <div class="amenity" style="left:271px;top:905px"><div class="amenity-circle"><svg width="52" height="52" viewBox="0 0 52 52" fill="none" stroke="#555" stroke-width="1.8"><rect x="6" y="6" width="40" height="40"/><path d="M6 19h40M6 32h40M26 6v40M14 12h4M34 12h4M14 25h4M34 25h4M14 38h4M34 38h4"/></svg></div><div class="amenity-label">Storage Space</div></div>
  <div class="amenity" style="left:396px;top:905px"><div class="amenity-circle"><svg width="56" height="50" viewBox="0 0 56 50" fill="none" stroke="#555" stroke-width="1.8"><rect x="4" y="10" width="48" height="6"/><path d="M10 16l-3 26M46 16l3 26M16 16l-2 18M40 16l2 18M16 22h24"/></svg></div><div class="amenity-label">Study Desk</div></div>
  <div class="amenity" style="left:521px;top:905px"><div class="amenity-circle"><svg width="50" height="56" viewBox="0 0 50 56" fill="none" stroke="#555" stroke-width="1.8"><rect x="9" y="4" width="32" height="46"/><path d="M25 4v46M9 14h32M20 28v6M30 28v6M12 50v3M38 50v3"/><circle cx="33" cy="21" r="4"/></svg></div><div class="amenity-label">Wardrobe</div></div>
  <div class="amenity" style="left:646px;top:905px"><div class="amenity-circle"><svg width="52" height="54" viewBox="0 0 52 54" fill="none" stroke="#555" stroke-width="1.8"><rect x="6" y="4" width="40" height="46"/><path d="M6 10h40M12 10v40M40 10v40"/><path d="M28 16v6h4M30 26v2M33 26v2M30 31v2M33 31v2"/></svg></div><div class="amenity-label">Ensuite Shower</div></div>
  <div class="amenity" style="left:771px;top:905px"><div class="amenity-circle"><svg width="56" height="52" viewBox="0 0 56 52" fill="none" stroke="#555" stroke-width="1.8"><rect x="6" y="4" width="18" height="12"/><rect x="32" y="4" width="18" height="12"/><rect x="4" y="28" width="48" height="20"/><path d="M4 34h48M28 34v14M10 24h10M36 24h10v4M14 40h6M36 40h6"/></svg></div><div class="amenity-label">Kitchenette</div></div>

  <div class="divider" style="top:1110px"></div>

  <h2 class="section-title" style="top:1185px">Public Amenities</h2>
  <div class="search-bar">
    <div class="search-input"><svg width="14" height="20" viewBox="0 0 14 20"><path d="M7 0a7 7 0 0 0-7 7c0 5 7 13 7 13s7-8 7-13a7 7 0 0 0-7-7z" fill="#aaa"/></svg>Type your location</div>
    <div class="transport-tab" style="width:123px"><svg width="16" height="18" viewBox="0 0 16 18" fill="none" stroke="#777" stroke-width="2"><rect x="2" y="1" width="12" height="12" rx="3"/><path d="M2 8h12M4 17l2-4M12 17l-2-4"/></svg>Trains</div>
    <div class="transport-tab" style="width:137px"><svg width="16" height="18" viewBox="0 0 16 18" fill="none" stroke="#777" stroke-width="2"><rect x="1" y="1" width="14" height="13" rx="2"/><path d="M1 8h14M4 14v3M12 14v3"/></svg>Busses</div>
    <div class="transport-tab active" style="width:106px"><svg width="18" height="14" viewBox="0 0 18 14"><path d="M3 6l2-5h8l2 5h2v6h-2v2h-2v-2H5v2H3v-2H1V6z" fill="#3276b5"/></svg>Car</div>
  </div>
  <div class="map" role="img" aria-label="Street map of the surrounding area with a location pin">
    <svg style="position:absolute;left:434px;top:70px" width="18" height="26" viewBox="0 0 18 26"><path d="M9 0a9 9 0 0 0-9 9c0 7 9 17 9 17s9-10 9-17a9 9 0 0 0-9-9z" fill="#2f62ac"/><circle cx="9" cy="9" r="3.5" fill="#fff"/></svg>
  </div>
</main>

<footer class="site-footer">
  <div class="footer-heading" style="left:144px">Links</div>
  <div class="footer-link" style="left:144px;top:91px">Home</div>
  <div class="footer-link" style="left:144px;top:118px">Profile</div>
  <div class="footer-link" style="left:144px;top:145px">Bond &amp; Rents</div>
  <div class="footer-link" style="left:144px;top:172px">Contact Us</div>
  <div class="footer-link" style="left:242px;top:91px">Schedule an Inspection</div>
  <div class="footer-link" style="left:242px;top:118px">Register</div>
  <div class="footer-link" style="left:242px;top:145px">Login</div>

  <div class="footer-heading" style="left:412px">Aliquam</div>
  <div class="footer-link" style="left:412px;top:91px">Donec vestibulum</div>
  <div class="footer-link" style="left:412px;top:118px">Quisque aliquet</div>
  <div class="footer-link" style="left:412px;top:145px">Pellentesque</div>
  <div class="footer-link" style="left:412px;top:172px">Etiam id</div>
  <div class="footer-link" style="left:531px;top:91px">Fusce vitae</div>
  <div class="footer-link" style="left:531px;top:118px">Aenean placerat</div>
  <div class="footer-link" style="left:531px;top:145px">Vestibulum ante</div>
  <div class="footer-link" style="left:531px;top:172px">Vestibulum eget</div>

  <div class="footer-heading" style="left:670px">Newsletter Signup</div>
  <div class="newsletter">Email Address<svg width="20" height="15" viewBox="0 0 20 15"><rect width="20" height="15" rx="1.5" fill="#333"/><path d="M1 1l9 7 9-7" stroke="#e9e9e9" stroke-width="1.6" fill="none"/></svg></div>

  <div class="footer-heading" style="left:937px">Follow us on</div>
  <div class="social" style="left:935px" aria-label="Social link"></div>
  <div class="social" style="left:984px" aria-label="Social link"></div>
  <div class="social" style="left:1034px" aria-label="Social link"></div>

  <div class="footer-rule"></div>
  <div class="copyright">Copyright © 2019 LodGivo. &nbsp; All rights reserved.</div>
</footer>

</body>
</html>
```